Hop Along Days campaign: promoting kids play in the UK - Website Redesign

Hop Along Days is a national UK campaign that promotes the value of play for children. The current website is live at http://www.hopalongdays.co.uk. This website has been live for 4 years and now needs to be redesigned. The target audience is parents of young children up to the age of 12.

The current site was designed with a series of old adverts in mind. Here is an example of an old advert: http://vidshare.example/qR7tLm2XwZa

Criticisms of existing site:
The design represented the adverts too closely. The result was a website that mirrors the adverts rather than complements them.
The color scheme is too dark.
Text-heavy pages (e.g. http://www.hopalongdays.co.uk/fun.php) are dull and not FUN!

New site
We have recently had a series of new video adverts produced:
advert 1: http://vidshare.example/hB4nVc8JsPe
advert 2: http://vidshare.example/KgW3rTy9DuM
advert 3: http://vidshare.example/zA5oEi1HbNq

The new site should be cleaner and brighter than the existing site, possibly with a white background using graphics, fonts and advert characters (see attached character graphics files) to add the element of fun and play.

The homepage should include:
1. Hop Along Days logo (attached)
2. Social Media links (visible on all pages of the site) – Chatterbook, Chirpline, ClipVault
3. Link to the HopAlongDays app page of the site (visible on all pages)
4. Image/video placeholder that the user can scroll through, view full-size images and play videos.
5. Text area to hold approximately 100 words describing the purpose of the campaign
6. Site footer to contain the same information as on the existing site along with the Northern Games & Crafts Guild logo (attached)

Site structure:
One change to the site structure… the “Brought to you by” menu item will be removed from the top-level menu.

General:
Some pages on the existing site are quite text-heavy, we would like to break up text on these pages in some way. Graphical division of paragraphs, use of advert characters?

Please note that all attached graphics file are the property of the Northern Games & Crafts Guild and must only be used for the purpose of this project.

```html
<!DOCTYPE html>
<html lang="en">
<head>
<meta charset="utf-8">
<title>Hop Along Days – Home</title>
<link rel="stylesheet" href="https://fonts.googleapis.com/css2?family=Bubblegum+Sans&family=Open+Sans:wght@400;600;700&display=swap">
<style>
:root{
  --purple:#5b3f9e;
  --pink:#e8457a;
  --blue:#1aaee6;
  --yellow:#f4c60a;
  --green:#a9c931;
  --rose:#ef5b84;
  --fb:#3b5b9a;
  --link:#3a6fb7;
  --text:#5a5a5a;
  --muted:#9a9a9a;
  --page:#f6f6f6;
  --line:#dcdcdc;
}
*{box-sizing:border-box;margin:0;padding:0}
html,body{width:876px;height:1200px;overflow:hidden}
body{font-family:"Open Sans",sans-serif;color:var(--text);background:var(--page)}
.canvas{position:relative;width:876px;height:1200px;overflow:hidden;background:var(--page)}
.abs{position:absolute}

/* header */
.sky{left:0;top:0;width:876px;height:190px;background:linear-gradient(#6ccdf2 0%,#a9e1f7 45%,var(--page) 100%)}
.brand{left:101px;top:40px;display:flex;align-items:center;gap:6px;font-family:"Bubblegum Sans",cursive;font-size:21px;color:var(--purple);line-height:1;white-space:nowrap}
.brand-dot{width:12px;height:12px;border-radius:50%;background:var(--pink);flex:none}
.nav{top:37px;left:0;width:876px;height:27px}
.nav a{position:absolute;top:0;height:27px;display:flex;align-items:center;justify-content:center;font-family:"Bubblegum Sans",cursive;font-size:12.5px;color:#3b2a12;text-decoration:none;background:var(--yellow);border:2px solid #e39a00;border-radius:8px;box-shadow:0 2px 0 #c98400;white-space:nowrap}
.nav a.current{background:var(--blue);color:#fff;border-color:#4b35a0;box-shadow:0 2px 0 #3a2a80}
.nav .string{position:absolute;top:-37px;width:1.5px;height:37px;background:#c0263a}

/* hero */
.hero{left:96px;top:95px;width:418px;height:274px;background:radial-gradient(circle at 50% 55%,#f3c9a8 0%,#e07aa0 35%,#c83a5a 60%,#6a9a3a 100%)}
.slide-arrow{top:212px;width:22px;height:44px;background:var(--green);border:2px solid #fff}
.slide-arrow.left{left:96px;border-radius:0 22px 22px 0}
.slide-arrow.right{left:492px;border-radius:22px 0 0 22px}
.play{left:278px;top:204px}

.tile{width:126px;display:flex;justify-content:center}
.tile .figure{position:absolute;left:25px;top:8px;width:76px;height:105px;border-radius:36px 36px 8px 8px;opacity:.55}
.tile .label{position:absolute;left:6px;width:114px;height:28px;display:flex;align-items:center;justify-content:center;font-family:"Bubblegum Sans",cursive;font-size:14px;background:rgba(255,255,255,.55);white-space:nowrap}

/* section headings */
.heading-row{display:flex;align-items:flex-end;gap:4px}
.heading{font-size:13px;font-weight:600;letter-spacing:.2px;white-space:nowrap;line-height:16px}
.heading .a{color:var(--purple)}
.heading .b{color:var(--pink)}
.heading-row .rule{flex:1;height:1px;background:var(--pink);margin-bottom:2px}

.idea{left:96px;top:426px;width:409px;height:164px;background:var(--blue)}
.idea-figure{left:18px;top:14px;width:130px;height:142px;border-radius:60px 60px 10px 10px;background:linear-gradient(#f6d88a,#e4574f 60%,#8bcfbf)}
.idea-text{left:153px;top:5px;width:232px;font-size:9.6px;line-height:14.3px;color:#fff;text-align:justify;overflow:hidden;height:153px}
.scrollbar{left:395px;top:0;width:14px;height:164px;background:#f7b320}
.scrollbar .thumb{position:absolute;left:2px;top:38px;width:10px;height:40px;background:#f08a5a;border-radius:2px}

.app{left:521px;top:426px;width:259px;height:164px;background:var(--green);overflow:hidden}
.phone{left:6px;top:11px;width:102px;height:145px;border-radius:12px;background:#1d1d1d}
.phone .screen{position:absolute;left:8px;top:13px;width:86px;height:110px;background:#fff;border-radius:3px;display:flex;align-items:center;justify-content:center;text-align:center;font-family:"Bubblegum Sans",cursive;font-size:13px;line-height:15px;color:var(--purple)}
.phone .home{position:absolute;left:45px;top:129px;width:11px;height:11px;border-radius:50%;border:2px solid #fff}
.app-girl{left:200px;top:8px;width:54px;height:150px;border-radius:28px 28px 6px 6px;background:linear-gradient(#c98a55,#5cc0a0 55%,#e26b7b)}
.app-title{left:104px;top:12px;width:110px;text-align:center;font-family:"Bubblegum Sans",cursive;font-size:14px;line-height:17.5px;color:#5a3a1a;white-space:nowrap}
.store{left:87px;width:132px;height:23px;display:flex;align-items:center;gap:5px;padding-left:6px;font-size:8.3px;font-weight:600;color:#fff;white-space:nowrap}
.store .dot{width:11px;height:11px;border-radius:50%;background:#fff;flex:none}
.store.robo{background:var(--rose)}
.store.fruit{background:var(--blue)}

.intro-row{left:96px;top:603px;width:370px}
.intro-row .heading{font-size:14px;line-height:18px}
.intro{left:96px;top:624px;width:682px;font-size:9.6px;line-height:14.3px;color:var(--text)}

/* columns */
.panel{top:740px;height:255px;background:#fff;border:1px solid var(--line)}
.activity{left:101px;width:218px;border-color:var(--fb)}
.activity .bar{height:30px;background:var(--fb);color:#fff;display:flex;align-items:center;justify-content:space-between;padding:0 8px;font-size:10px}
.activity .bar b{font-weight:700;font-size:10.5px}
.avatar{position:absolute;width:49px;height:49px;border:1px solid var(--line);background:linear-gradient(#cfd3d6,#6b6f72)}
.entry-text{position:absolute;font-size:10px;line-height:13.5px;white-space:nowrap}
.entry-text .title,.entry-text .body{color:var(--link)}
.entry-text .meta{font-size:8px;color:var(--muted);margin-top:5px}
.plugin{position:absolute;left:8px;bottom:4px;display:flex;align-items:center;gap:4px;font-size:7px;color:#666;border-top:1px solid var(--line);width:200px;padding-top:4px}
.plugin i{width:9px;height:9px;background:var(--fb);display:block}

.tweets{left:328px;width:219px}
.tweets .bar{height:34px;display:flex;align-items:center;justify-content:space-between;padding:0 4px 0 8px;border-bottom:1px solid var(--line);font-size:12.5px;color:#333}
.follow{height:21px;padding:0 6px;display:flex;align-items:center;gap:5px;font-size:9px;font-weight:600;color:#333;background:linear-gradient(#fff,#e4e4e4);border:1px solid #c8c8c8;border-radius:3px;white-space:nowrap}
.follow i{width:10px;height:10px;border-radius:50%;background:#2aa9e0;display:block}
.tweet-text{position:absolute;left:59px;width:156px;font-size:10px;line-height:13.5px;color:#444;white-space:nowrap}
.tweet-text .who{color:#333;display:flex}
.tweet-text .who .h{color:var(--muted);margin-left:3px;margin-right:auto}
.tweet-text .who .t{color:var(--muted)}
.tweet-text .handle{color:var(--blue)}
.sep{position:absolute;left:0;width:100%;height:1px;background:var(--line)}
.tweet-box{position:absolute;left:6px;top:230px;width:205px;height:22px;border:1px solid #c8c8c8;border-radius:4px;font-size:9px;color:#666;display:flex;align-items:center;padding-left:8px}

.videos{left:556px;width:218px}
.thumb{position:absolute;left:6px;width:64px;height:49px;background:linear-gradient(135deg,#2a2a2a,#7a2020 50%,#3a4a6a);border:2px solid #d8d8d8}
.thumb .time{position:absolute;right:3px;bottom:2px;font-size:9px;font-weight:700;color:#fff}
.thumb svg{position:absolute;left:24px;top:14px}
.video-text{position:absolute;left:78px;width:136px;font-size:9.4px;line-height:13px;color:#555;white-space:nowrap}
.video-text .title{color:#333}
.video-text .meta{font-size:7.8px;line-height:11px;color:var(--muted);margin-top:1px}

/* decorations */
.cat{left:788px;top:298px;width:88px;height:210px;background:linear-gradient(#8a5a2a 0 6%,transparent 6%),linear-gradient(#f3c77a,#e0a64a);border-radius:0 0 30px 30px;opacity:.85}
.tree{left:0;top:867px;width:92px;height:158px;background:radial-gradient(ellipse at 50% 35%,#6fb83a 0 55%,transparent 56%),linear-gradient(90deg,transparent 42%,#7a4a22 42% 56%,transparent 56%)}
.grass{left:0;top:985px}

/* footer */
.footer{left:0;top:1029px;width:876px;height:171px;background:#efefef}
.mascots{left:9px;top:1043px;width:149px;height:153px;border-radius:60px 60px 20px 20px;background:linear-gradient(120deg,#3a7ad8 0 40%,#f3a0c8 40% 100%)}
.f-head{font-size:10.5px;font-weight:600;color:var(--purple);letter-spacing:.2px}
.f-list{list-style:none;font-size:10px;line-height:16.6px;color:var(--purple)}
.f-list li{display:flex;align-items:center;gap:6px}
.f-list .tri{width:0;height:0;border-left:4px solid var(--purple);border-top:3px solid transparent;border-bottom:3px solid transparent}
.contact{font-size:10px;line-height:16.6px;color:var(--purple);white-space:nowrap}
.social{display:flex;align-items:center;gap:8px;font-size:10px;color:var(--purple);height:18px}
.social i{width:17px;height:17px;border-radius:50%;background:#d8d8d8;border:2px solid #fff;box-shadow:0 0 0 1px #ccc;display:block}
.guild{left:592px;top:1099px;width:82px;font-size:10px;font-weight:700;line-height:13px;color:#333;text-align:center}
.dog{left:788px;top:1112px;width:66px;height:80px;border-radius:30px 30px 10px 10px;background:linear-gradient(#fff,#f3d9a0)}
.footer-brand{left:686px;top:1106px;font-family:"Bubblegum Sans",cursive;font-size:15px;color:var(--purple);white-space:nowrap}
</style>
</head>
<body>
<div class="canvas">

  <div class="abs sky" role="img" aria-label="Cartoon sky with soft white clouds"></div>

  <div class="abs brand"><span class="brand-dot"></span>Hop Along Days</div>

  <nav class="abs nav">
    <a class="current" href="#" style="left:300px;width:89px"><span class="string" style="left:44px"></span>Play Right Now</a>
    <a href="#" style="left:406px;width:79px"><span class="string" style="left:39px"></span>Get Invloved</a>
    <a href="#" style="left:505px;width:80px"><span class="string" style="left:39px"></span>Why Play</a>
    <a href="#" style="left:603px;width:79px"><span class="string" style="left:39px"></span>Fun Forever</a>
    <a href="#" style="left:699px;width:81px"><span class="string" style="left:40px"></span>Resources</a>
  </nav>

  <div class="abs hero" role="img" aria-label="Photo of smiling children lying in a circle on the grass, making binoculars with their hands"></div>
  <div class="abs slide-arrow left"><svg width="18" height="40" viewBox="0 0 18 40"><path d="M11 13 L4 20 L11 27 Z" fill="#fff"/></svg></div>
  <div class="abs slide-arrow right"><svg width="18" height="40" viewBox="0 0 18 40"><path d="M7 13 L14 20 L7 27 Z" fill="#fff"/></svg></div>
  <svg class="abs play" width="54" height="54" viewBox="0 0 54 54">
    <circle cx="27" cy="27" r="25" fill="var(--yellow)" stroke="#fff" stroke-width="2"/>
    <circle cx="27" cy="27" r="19" fill="#5b3f9e"/>
    <path d="M22 17 L37 27 L22 37 Z" fill="var(--yellow)"/>
  </svg>

  <div class="abs tile" style="left:521px;top:95px;height:130px;background:var(--green)">
    <div class="figure" role="img" aria-label="Cartoon girl with a blue bow holding a sign" style="background:#f1d36a"></div>
    <div class="label" style="top:86px;color:#fff">PLAY RIGHT NOW</div>
  </div>
  <div class="abs tile" style="left:654px;top:95px;height:130px;background:var(--yellow)">
    <div class="figure" role="img" aria-label="Cartoon girl with bunches holding a sign" style="background:#6b3a20"></div>
    <div class="label" style="top:91px;color:#fff">GET INVOLVED</div>
  </div>
  <div class="abs tile" style="left:521px;top:232px;height:137px;background:var(--blue)">
    <div class="figure" role="img" aria-label="Cartoon girl in a red coat holding a sign" style="background:#d84a5a"></div>
    <div class="label" style="top:87px;color:var(--purple)">WHY PLAY</div>
  </div>
  <div class="abs tile" style="left:654px;top:232px;height:137px;background:var(--rose)">
    <div class="figure" role="img" aria-label="Cartoon red-haired girl holding a sign" style="background:#f1a04a"></div>
    <div class="label" style="top:87px;color:var(--purple)">FUN FOREVER</div>
  </div>

  <div class="abs cat" role="img" aria-label="Cartoon ginger cat hanging from a branch"></div>

  <div class="abs heading-row" style="left:96px;top:391px;width:410px"><div class="heading"><span class="a">PLAY IDEA </span><span class="b">OF THE DAY</span></div><div class="rule"></div></div>
  <div class="abs heading-row" style="left:523px;top:391px;width:257px"><div class="heading"><span class="a">HOP ALONG DAYS </span><span class="b">APP</span></div><div class="rule"></div></div>

  <section class="abs idea">
    <div class="abs idea-figure" role="img" aria-label="Cartoon girl holding a wand with a glowing light bulb idea"></div>
    <p class="abs idea-text">Lorem ipsum dolor sit amet, cons ectetuer adipis cinl gere elit, sed diam enonummy nibh cinl gere tincidut ufgkdtil erererer errrlaoreetna all dolore magna ali quaeml erat volutpaterUtmagna diam wisi enii mad minimerrrlaoreetna Utmagna diam wisi enii mad minimerrrlaoreetna rmererrmliUtmagna diam wisi enii mad minimerrrlaoreetna rmerermli olore mq allerrrlaoreetna allUtmagna diam wisi enii mad minimerrrlaoreetna sed diam enonummy nibh cinl gere tincidut ufgkdtil erererer errrlaoreetna all doloreUtmagna diam sed diam enonummy nibh cinl</p>
    <div class="abs scrollbar">
      <svg width="14" height="12" viewBox="0 0 14 12" style="position:absolute;top:0"><path d="M3 8 L7 4 L11 8 Z" fill="#e8457a"/></svg>
      <div class="thumb"></div>
      <svg width="14" height="12" viewBox="0 0 14 12" style="position:absolute;bottom:0"><path d="M3 4 L7 8 L11 4 Z" fill="#e8457a"/></svg>
    </div>
  </section>

  <section class="abs app">
    <div class="abs phone"><div class="screen">Hop Along<br>Days</div><div class="home"></div></div>
    <div class="abs app-girl" role="img" aria-label="Cartoon girl with glasses in a green dress and striped tights"></div>
    <div class="abs app-title">Get the<br>Hop Along Days<br>App on your<br>Mobile Now</div>
    <div class="abs store robo" style="top:111px"><span class="dot"></span>Available on Robo Market</div>
    <div class="abs store fruit" style="top:140px"><span class="dot"></span>Available on Fruit Store</div>
  </section>

  <div class="abs heading-row intro-row"><div class="heading"><span class="a">Lorem ipsum </span><span class="b">sid amet</span></div><div class="rule"></div></div>
  <p class="abs intro">Lorem ipsum dolor sit amet, cons ectetuer adipis cinl gere elit, sed diam enonummy nibh tincidut ufgkdtil erererer errrlaoreetna all dolore magna ali quaeml erat volutpater Ut wisi enii mad minimerrm.Sed diam enonummy nibhereierii tincidut ufgkdtiere e rere errrlaoreetna allii dolore magna ali quae merat ererer rmerermli quae m erat volutpat. Enonummy nibh tincidut ufgkdtierereercfd errrlaorei etna all dolore magna ali quae m erat volutpaerererii mpr e o ereer ali qae merat. Lorem ipsum dolor sit amet, cons ectetuer adipis cinl gere elit, sed diam enonummy nibh tincidut ufgkdtil erererer errrlaoreetna all dolore magna ali quaeml erat volutpater Ut wisi enii mad minimerrm.Sed diam enonummy nibhereierii tincidut ufgkdtiere e rere errrlaoreetna allii dolore magna ali quae merat ereieerer rmerermli quae m erat volutpat. Enonummy nibh tincidut ufgkdtierereercfd errrlaorei etna all dolore magna ali quae m erat volutpaerererii mpr e o ereer ali quae merat.</p>

  <div class="abs tree" role="img" aria-label="Cartoon leafy tree"></div>
  <svg class="abs grass" width="876" height="46" viewBox="0 0 876 46" role="img" aria-label="Rolling green grass">
    <defs><linearGradient id="grassFill" x1="0" y1="0" x2="0" y2="1"><stop offset="0" stop-color="#8fd13a"/><stop offset="1" stop-color="#5fae2a"/></linearGradient></defs>
    <path d="M0 20 C120 8 240 30 360 24 C480 18 560 2 680 14 C760 22 820 14 876 10 L876 46 L0 46 Z" fill="url(#grassFill)"/>
  </svg>

  <section class="abs panel activity">
    <div class="bar"><span>Recent Activity</span><b>Chatterbook</b></div>
    <div class="avatar" role="img" aria-label="Member profile photo" style="left:8px;top:36px"></div>
    <div class="entry-text" style="left:62px;top:34px"><div class="title">Lorem fdaafipsum dafsdolor</div><div class="body">sit amet, coctetuer adipiscing<br>elit, sed diam</div><div class="meta">2 people recommended this.</div></div>
    <div class="avatar" role="img" aria-label="Member profile photo" style="left:8px;top:104px"></div>
    <div class="entry-text" style="left:62px;top:102px"><div class="title">Lorem fdaafipsum dafsdolor</div><div class="body">sit amet, coctetuer adipiscing<br>elit, sed diam</div><div class="meta">2 people recommended this.</div></div>
    <div class="avatar" role="img" aria-label="Member profile photo" style="left:8px;top:172px"></div>
    <div class="entry-text" style="left:62px;top:170px"><div class="title">Lorem fdaafipsum dafsdolor</div><div class="body">sit amet, coctetuer adipiscing<br>elit, sed diam</div><div class="meta">2 people recommended this.</div></div>
    <div class="plugin"><i></i>Chatterbook social plugin</div>
  </section>

  <section class="abs panel tweets">
    <div class="bar"><span>Tweets</span><span class="follow"><i></i>Follow @ HopAlongPlay</span></div>
    <div class="avatar" role="img" aria-label="Profile photo" style="left:6px;top:42px"></div>
    <div class="tweet-text" style="top:39px"><div class="who">Tom Fenwick<span class="h">@tomfenwick</span><span class="t">18h</span></div>sit amet, coctetuer adipiscing<br>elit, sed diam <span class="handle">@hopalongplay</span><br>sit amet, consectetu</div>
    <div class="sep" style="top:106px"></div>
    <div class="avatar" role="img" aria-label="Profile photo" style="left:6px;top:110px"></div>
    <div class="tweet-text" style="top:107px"><div class="who">Tom Fenwick<span class="h">@tomfenwick</span><span class="t">18h</span></div>sit amet, coctetuer adipiscing<br>elit, sed diam <span class="handle">@hopalongplay</span><br>sit amet, consectetu</div>
    <div class="sep" style="top:174px"></div>
    <div class="avatar" role="img" aria-label="Profile photo" style="left:6px;top:177px"></div>
    <div class="tweet-text" style="top:174px"><div class="who">Tom Fenwick<span class="h">@tomfenwick</span><span class="t">18h</span></div>sit amet, coctetuer adipiscing<br>elit, sed diam <span class="handle">@hopalongplay</span></div>
    <div class="tweet-box">Tweet to @hopalongplay</div>
  </section>

  <section class="abs panel videos">
    <div class="thumb" role="img" aria-label="Video still from advert" style="top:5px"><svg width="14" height="18" viewBox="0 0 14 18"><path d="M1 1 L13 9 L1 17 Z" fill="#fff"/></svg><span class="time">1:44</span></div>
    <div class="video-text" style="top:2px"><div class="title">Lorem fdaafipsum dafsdolor</div>sit amet, coctetuer adipiscing<br>elit, sed diam<div class="meta">1 Day ago &nbsp;| &nbsp;2345,views</div></div>
    <div class="sep" style="top:63px"></div>
    <div class="thumb" role="img" aria-label="Video still from advert" style="top:70px"><svg width="14" height="18" viewBox="0 0 14 18"><path d="M1 1 L13 9 L1 17 Z" fill="#fff"/></svg><span class="time">3:31</span></div>
    <div class="video-text" style="top:66px"><div class="title">Lorem fdaafipsum dafsdolor</div>sit amet, coctetuer adipiscing<br>elit, sed diam<div class="meta">1 Day ago &nbsp;| &nbsp;2345,views</div></div>
    <div class="sep" style="top:127px"></div>
    <div class="thumb" role="img" aria-label="Video still from advert" style="top:134px"><svg width="14" height="18" viewBox="0 0 14 18"><path d="M1 1 L13 9 L1 17 Z" fill="#fff"/></svg><span class="time">2:14</span></div>
    <div class="video-text" style="top:130px"><div class="title">Lorem fdaafipsum dafsdolor</div>sit amet, coctetuer adipiscing<br>elit, sed diam<div class="meta">1 Day ago &nbsp;| &nbsp;2345,views</div></div>
    <div class="sep" style="top:191px"></div>
    <div class="thumb" role="img" aria-label="Video still from advert" style="top:198px"><svg width="14" height="18" viewBox="0 0 14 18"><path d="M1 1 L13 9 L1 17 Z" fill="#fff"/></svg><span class="time">13:13</span></div>
    <div class="video-text" style="top:194px"><div class="title">Lorem fdaafipsum dafsdolor</div>sit amet, coctetuer adipiscing<br>elit, sed diam<div class="meta">1 Day ago &nbsp;| &nbsp;2345,views</div></div>
  </section>

  <footer class="abs footer"></footer>
  <div class="abs mascots" role="img" aria-label="Two cartoon mer-children mascots"></div>

  <div class="abs f-head" style="left:166px;top:1066px">QUICK LINKS</div>
  <ul class="abs f-list" style="left:166px;top:1088px">
    <li><span class="tri"></span>Play Right Now</li>
    <li><span class="tri"></span>Get Invloved</li>
    <li><span class="tri"></span>Why Play</li>
    <li><span class="tri"></span>Fun Forever</li>
    <li><span class="tri"></span>Resources</li>
  </ul>

  <div class="abs f-head" style="left:277px;top:1066px">QUICK CONTACT</div>
  <svg class="abs" style="left:273px;top:1092px" width="10" height="13" viewBox="0 0 10 13"><path d="M5 0 C2 0 0 2 0 5 C0 8 5 13 5 13 C5 13 10 8 10 5 C10 2 8 0 5 0 Z" fill="var(--pink)"/><circle cx="5" cy="5" r="2" fill="#efefef"/></svg>
  <div class="abs contact" style="left:293px;top:1088px">Hop Along Days<br>14 Marlow Lane<br>Leeds,<br>LS2 7QT</div>
  <svg class="abs" style="left:274px;top:1159px" width="11" height="8" viewBox="0 0 11 8"><rect x=".5" y=".5" width="10" height="7" fill="none" stroke="var(--pink)"/><path d="M.5 .5 L5.5 4.5 L10.5 .5" fill="none" stroke="var(--pink)"/></svg>
  <div class="abs contact" style="left:293px;top:1155px">getinvolved@hopalongdays.co.uk</div>

  <div class="abs f-head" style="left:489px;top:1069px">FOLLOW US</div>
  <div class="abs social" style="left:489px;top:1094px"><i></i>Chatterbook</div>
  <div class="abs social" style="left:489px;top:1123px"><i></i>Chirpline</div>
  <div class="abs social" style="left:489px;top:1152px"><i></i>ClipVault</div>

  <div class="abs guild">Northern Games &amp; Crafts Guild</div>
  <div class="abs dog" role="img" aria-label="Cartoon puppy mascot"></div>
  <div class="abs footer-brand">Hop Along Days</div>

</div>
</body>
</html>
```